Design a compelling Tarnwove Business Card that will drive people to my site

I want a business card that I can give to people—less to tell them who I am and more to direct them to my website. My website is a portal for Pelmor Aquatics Officials and a place for people who want to become Pelmor Aquatics Officials.
I am uploading my official company logo as well as a business card mockup that I did on my own. Please feel free to completely stray from this design.
I've included a screen recording of the homepage of my website as well.
Target Market(s)
Pelmor Aquatics Officials and people who desire to become one
Contact Information for Business Card
website url
Look and feel
Each slider illustrates characteristics of the customer's brand and the style your logo design should communicate.

```html
<!DOCTYPE html>
<html lang="en">
<head>
<meta charset="utf-8">
<title>Tarnwove Business Card</title>
<link href="https://fonts.googleapis.com/css2?family=Montserrat:wght@400;500;700;800&display=swap" rel="stylesheet">
<style>
  :root {
    --card-blue: #3a55a8;
    --card-blue-deep: #344d9c;
    --accent-light: #93a6d8;
    --ink-blue: #2f4a9c;
    --paper: #ffffff;
    --stage: #3a3a3d;
  }
  html, body {
    margin: 0;
    width: 1200px;
    height: 915px;
    overflow: hidden;
    background: var(--stage);
    font-family: "Montserrat", sans-serif;
  }
  .canvas { position: relative; width: 1200px; height: 915px; }
  .card {
    position: absolute;
    width: 520px;
    height: 297px;
    border-radius: 18px;
    overflow: hidden;
    background: var(--card-blue);
    box-shadow: 0 12px 30px rgba(0,0,0,0.35);
  }
  .card-front { left: 90px; top: 110px; }
  .card-back { left: 590px; top: 490px; }

  .bubble-field {
    position: absolute; inset: 0;
    background:
      radial-gradient(circle at 78% 22%, rgba(255,255,255,0.12), transparent 28%),
      radial-gradient(circle at 20% 75%, rgba(255,255,255,0.08), transparent 25%),
      linear-gradient(135deg, var(--card-blue), var(--card-blue-deep));
  }
  .wordmark {
    position: absolute;
    display: flex; align-items: center; gap: 12px;
    font-weight: 800;
    letter-spacing: -1px;
    line-height: 1;
  }
  .wordmark-dot { border-radius: 50%; flex: none; }
  .card-front .wordmark {
    left: 0; right: 0; top: 118px; justify-content: center;
    font-size: 62px; color: var(--paper);
  }
  .card-front .wordmark-dot { width: 22px; height: 22px; background: var(--paper); }

  .back-art { position: absolute; inset: 0; }
  .card-back .wordmark {
    left: 238px; top: 58px; gap: 10px;
    font-size: 44px; color: var(--ink-blue);
  }
  .card-back .wordmark-dot { width: 15px; height: 15px; background: var(--ink-blue); }

  .contact { position: absolute; left: 34px; top: 160px; color: var(--paper); }
  .contact-name { margin: 0; font-size: 19px; line-height: 23px; font-weight: 700; color: var(--accent-light); }
  .contact-role { margin: 1px 0 0; font-size: 13px; line-height: 16px; font-weight: 400; }
  .contact-rule { width: 22px; height: 1px; background: var(--accent-light); margin: 7px 0 7px; }
  .contact-list { list-style: none; margin: 0; padding: 0; }
  .contact-list li {
    display: flex; align-items: center; gap: 10px;
    font-size: 13px; line-height: 16px; margin-bottom: 4px;
  }
  .contact-icon {
    width: 16px; height: 16px; border-radius: 50%;
    border: 1px solid var(--accent-light);
    display: flex; align-items: center; justify-content: center; flex: none;
  }
</style>
</head>
<body>
<main class="canvas">

  <section class="card card-front" aria-label="Card front">
    <div class="bubble-field" role="img" aria-label="Soft translucent bubble pattern over blue"></div>
    <div class="wordmark"><span class="wordmark-dot"></span>tarnwove</div>
  </section>

  <section class="card card-back" aria-label="Card back">
    <svg class="back-art" viewBox="0 0 520 297" preserveAspectRatio="none" aria-hidden="true">
      <path d="M140 0 C 200 150, 370 175, 520 125 L 520 0 Z" fill="var(--paper)"/>
      <path d="M131 0 C 192 158, 370 186, 520 134" fill="none" stroke="var(--accent-light)" stroke-width="7"/>
      <path d="M123 0 C 185 166, 370 195, 520 141" fill="none" stroke="var(--paper)" stroke-width="2"/>
    </svg>
    <div class="wordmark"><span class="wordmark-dot"></span>tarnwove</div>

    <div class="contact">
      <h2 class="contact-name">Daniel Ferrante</h2>
      <p class="contact-role">CEO &amp; Founder</p>
      <div class="contact-rule"></div>
      <ul class="contact-list">
        <li>
          <span class="contact-icon">
            <svg width="9" height="9" viewBox="0 0 10 10"><path d="M2 1 L4 1 L4.6 3 L3.4 3.8 Q4.4 5.8 6.2 6.6 L7 5.4 L9 6 L9 8 Q5 9 1.5 4.5 Q1 2 2 1 Z" fill="var(--accent-light)"/></svg>
          </span>(555) 217-4403
        </li>
        <li>
          <span class="contact-icon">
            <svg width="9" height="9" viewBox="0 0 10 10"><rect x="1" y="2.5" width="8" height="5.5" fill="none" stroke="var(--accent-light)" stroke-width="1"/><path d="M1 2.5 L5 5.5 L9 2.5" fill="none" stroke="var(--accent-light)" stroke-width="1"/></svg>
          </span>dan@tarnwove.com
        </li>
        <li>
          <span class="contact-icon">
            <svg width="9" height="9" viewBox="0 0 10 10"><circle cx="5" cy="5" r="4" fill="none" stroke="var(--accent-light)" stroke-width="0.9"/><ellipse cx="5" cy="5" rx="1.8" ry="4" fill="none" stroke="var(--accent-light)" stroke-width="0.8"/><path d="M1 5 H9" stroke="var(--accent-light)" stroke-width="0.8"/></svg>
          </span>www.tarnwove.com
        </li>
      </ul>
    </div>
  </section>

</main>
</body>
</html>
```